Brightbay Orthodontics business card design

Need a business card design that reflects our re-branding (orthodontic office - braces) and a new partnership with a pediatric dental office. We would like to include "for adults and children" on the card as well so adults know they are welcome to get their braces here as well. Office design is modern and would like business card to reflect a modern type look. Here's the text we would like to be included on the card:

Darren Wolcott, DDS, MSD
5214 West Linden Avenue, Suite 204
Harlow Springs, KS 76991
555-418-2637
www.brightbayortho.example
info@brightbayortho.example

Can we add the following to the existing designs? Darren Wolcott, DDS, MSD 5214 West Linden Avenue, Suite 204 Harlow Springs, KS 76991 555-418-2637

Does anyone have any more vertical designs available? Thanks!

Dental

```html
<!DOCTYPE html>
<html lang="en">
<head>
<meta charset="utf-8">
<title>Brightbay Orthodontics – Business Card</title>
<link rel="stylesheet" href="https://fonts.googleapis.com/css2?family=Fredoka:wght@600&family=Alegreya+SC:wght@800&family=Griffy&display=swap">
<style>
  :root {
    --paper: #ffffff;
    --ink: #111111;
    --yellow: #fff200;
    --blue: #1b75bb;
    --magenta: #ec008c;
    --green: #8dc63f;
    --orange: #f7941d;
  }
  html, body {
    margin: 0;
    padding: 0;
    overflow: hidden;
    background: var(--paper);
  }
  .card {
    position: relative;
    width: 1200px;
    height: 686px;
    background: var(--paper);
    overflow: hidden;
  }
  .pattern-panel {
    position: absolute;
    left: 606px;
    top: 0;
    width: 594px;
    height: 686px;
    background: linear-gradient(160deg,
      var(--yellow) 0%, var(--magenta) 22%, var(--blue) 42%,
      var(--green) 62%, var(--orange) 82%, var(--magenta) 100%);
    opacity: 0.85;
  }
  .pattern-strip {
    position: absolute;
    left: 0;
    top: 646px;
    width: 606px;
    height: 40px;
    background: linear-gradient(90deg,
      var(--orange) 0%, var(--green) 25%, var(--blue) 50%,
      var(--magenta) 75%, var(--yellow) 100%);
    opacity: 0.85;
  }
  .brand {
    position: absolute;
    left: 40px;
    top: 60px;
    width: 540px;
    margin: 0;
    font-family: "Fredoka", sans-serif;
    font-weight: 600;
    color: var(--ink);
    text-align: center;
    line-height: 1;
  }
  .brand-name {
    display: block;
    font-size: 92px;
    letter-spacing: 1px;
  }
  .brand-practice {
    display: block;
    margin-top: 40px;
    font-size: 72px;
  }
  .colour-dashes {
    position: absolute;
    left: 91px;
    top: 402px;
    display: flex;
    gap: 13px;
  }
  .colour-dashes span {
    width: 74px;
    height: 14px;
  }
  .dash-yellow { background: var(--yellow); }
  .dash-blue { background: var(--blue); }
  .dash-magenta { background: var(--magenta); }
  .dash-green { background: var(--green); }
  .dash-orange { background: var(--orange); }
  .tagline {
    position: absolute;
    left: 40px;
    top: 470px;
    margin: 0;
    font-family: "Griffy", cursive;
    font-size: 48px;
    color: var(--ink);
    line-height: 76px;
    letter-spacing: 3px;
  }
  .tagline-second {
    display: block;
    padding-left: 140px;
  }
  .contact {
    position: absolute;
    right: 48px;
    top: 70px;
    text-align: right;
    font-family: "Alegreya SC", serif;
    font-weight: 800;
    font-style: normal;
    color: var(--paper);
    -webkit-text-stroke: 2px var(--ink);
    paint-order: stroke fill;
    text-shadow: 2px 2px 0 var(--ink);
  }
  .contact p { margin: 0; }
  .contact-name,
  .contact-credentials {
    font-size: 42px;
    line-height: 56px;
  }
  .contact-address {
    margin-top: 36px !important;
    font-size: 30px;
    line-height: 46px;
  }
  .contact-city {
    margin-top: 38px !important;
    font-size: 30px;
    line-height: 44px;
  }
  .contact-web {
    margin-top: 40px !important;
    font-size: 23px;
    line-height: 40px;
  }
  .contact-email {
    margin-top: 46px !important;
    font-size: 23px;
    line-height: 40px;
  }
</style>
</head>
<body>
  <div class="card">
    <div class="pattern-panel" role="img" aria-label="Colourful brick pattern in yellow, blue, magenta, green and orange"></div>
    <div class="pattern-strip" role="img" aria-label="Colourful brick pattern border along the bottom edge"></div>

    <h1 class="brand">
      <span class="brand-name">Brightbay</span>
      <span class="brand-practice">Orthodontics</span>
    </h1>

    <div class="colour-dashes" aria-hidden="true">
      <span class="dash-yellow"></span>
      <span class="dash-blue"></span>
      <span class="dash-magenta"></span>
      <span class="dash-green"></span>
      <span class="dash-orange"></span>
    </div>

    <p class="tagline">“for adults<span class="tagline-second">and children”</span></p>

    <address class="contact">
      <p class="contact-name">Darren Wolcott</p>
      <p class="contact-credentials">DDS, MSD</p>
      <p class="contact-address">5214 West Linden Avenue,<br>Suite 204</p>
      <p class="contact-city">Harlow Springs, KS 76991<br>555-418-2637</p>
      <p class="contact-web">www.brightbayortho.example</p>
      <p class="contact-email">info@brightbayortho.example</p>
    </address>
  </div>
</body>
</html>
```